Indonesian B2B Company (Bawo Ingredients) - Stationery Design

Bawo Ingredients needs a corporate, bold and professional-looking stationery design.

Bawo Ingredients is a new Indonesian company manufacturing, marketing and distributing various ingredients / raw materials such as flavours, fragrance, colours, sweeteners, preservatives for the food & beverage, pharmaceutical, personal care and other household goods industries.

It is a business to business (B2B) company as we supply various natural and synthetic raw materials to various consumer goods manufacturers. We therefore need a logo/identity with corporate and industrial style.

Bawo Ingredients is a startup company which belongs to a larger Tunas Mekar group of companies (http://tunasmekar.examplebiz.net/about) that focuses in the mining, petroleum and energy businesses. Bawo Ingredients would like to focus in providing good quality, safe, reliable and affordable ingredients for the industries. Our tagline is "Ingredients for Your Success"
Updates

We have updated some information including our requirements and contact details to be shown in the stationery. Please check the project brief.

Regards,

Bawo Ingredients

Target Market(s)

Manufacturers of food & beverages, personal care, pharmaceutical and other FMCG factories.

Industry/Entity Type

Business

Requirements
Must have
• Smart, professional and corporate touches in the stationery designs. We require designs for:
1. Letterhead
2. Envelope (with and without window)
3. Name card
4. Powerpoint presentation template
5. CD label
6. Small memo / with compliments card

Contact details:

Company name:
PT Bawo Ingredients

Address:
Ruko Puri Lestari Selatan, Blok F07 no: 11-12
Sunter Jaya Utara, 14350
Indonesia

Tel:+62 21 638 2097
Fax:+62 21 638 2096
Email: info@bawo-ingredients.co.id
Website: www.bawo-ingredients.co.id

```html
<!DOCTYPE html>
<html lang="en">
<head>
<meta charset="utf-8">
<title>Bawo Ingredients – Stationery</title>
<link href="https://fonts.googleapis.com/css2?family=Barlow:wght@400;500;700&display=swap" rel="stylesheet">
<style>
:root{
  --red:#d2232a;
  --red-dark:#a3151b;
  --ink:#3a3a3a;
  --grey:#7a7a7a;
  --paper:#ffffff;
  --backdrop:#e9e7e4;
  --rule:#c9c9c9;
}
*{box-sizing:border-box;margin:0;padding:0}
html,body{width:1200px;height:900px;overflow:hidden}
body{background:var(--backdrop);font-family:"Barlow",Arial,sans-serif;color:var(--ink);position:relative}
.sheet{position:absolute;background:var(--paper);box-shadow:0 2px 8px rgba(0,0,0,.18);overflow:hidden}
address{font-style:normal}

.brand{display:flex;align-items:center;gap:7px}
.brand-dot{background:var(--red);display:block;flex:none}
.brand-name{color:var(--ink);font-weight:500;white-space:nowrap;letter-spacing:.02em}

.web-tab{position:absolute;background:var(--red);color:#fff;font-weight:500;letter-spacing:.18em;display:flex;align-items:center;white-space:nowrap}
.base-line{position:absolute;left:0;right:0;bottom:0;background:var(--red)}

/* Letterhead */
.letterhead{left:50px;top:102px;width:495px;height:701px}
.letterhead .brand{position:absolute;left:34px;top:34px}
.letterhead .brand-dot{width:12px;height:12px}
.letterhead .brand-name{font-size:15px}
.letterhead .divider{position:absolute;left:343px;top:24px;width:1px;height:70px;background:var(--rule)}
.letterhead .contact{position:absolute;right:24px;top:26px;text-align:right;font-size:8.5px;line-height:1.35}
.contact .company{color:var(--red);font-weight:700;font-size:9.5px;margin-bottom:10px}
.contact .gap{height:10px}
.letterhead .web-tab{left:0;bottom:4px;width:235px;height:20px;padding-left:22px;font-size:9px;border-top-right-radius:10px}
.letterhead .base-line{height:4px}

/* Business card front */
.card-front{left:652px;top:120px;width:223px;height:120px}
.card-front .brand{position:absolute;left:14px;top:14px;gap:5px}
.card-front .brand-dot{width:7px;height:7px}
.card-front .brand-name{font-size:9.5px}
.card-front .person{position:absolute;left:14px;top:58px;font-size:5.5px;line-height:1.4;text-align:center;width:86px}
.card-front .person strong{display:block;color:var(--red);font-size:7px;font-weight:700}
.card-front .person .mob{margin-top:6px;text-align:left}
.card-front .contact{position:absolute;left:122px;top:34px;font-size:5px;line-height:1.35}
.card-front .contact .company{font-size:6px;margin-bottom:4px}
.card-front .contact .gap{height:5px}
.card-front .web-tab{right:0;bottom:2px;width:86px;height:10px;padding-left:8px;font-size:4.5px;border-top-left-radius:5px}
.card-front .base-line{height:2px}

/* Business card back */
.card-back{left:884px;top:120px;width:213px;height:120px;background:linear-gradient(135deg,var(--red) 0%,var(--red-dark) 100%)}
.card-back .brand{position:absolute;left:16px;top:44px}
.card-back .brand-name{color:#fff;font-size:12px}
.card-back .web{position:absolute;left:0;right:0;bottom:10px;text-align:center;color:#fff;font-size:5.5px;letter-spacing:.2em}

/* Envelope front */
.env-front{left:583px;top:273px;width:569px;height:247px}
.env-front .brand{position:absolute;left:30px;top:38px}
.env-front .brand-dot{width:11px;height:11px}
.env-front .brand-name{font-size:14px}
.env-front .web-tab{right:0;bottom:3px;width:230px;height:22px;padding-left:26px;font-size:9.5px;border-top-left-radius:11px}
.env-front .base-line{height:3px}

/* Envelope back */
.env-back{left:583px;top:537px;width:569px;height:251px}
.env-back svg.flap{position:absolute;inset:0}
.env-back .brand{position:absolute;left:0;right:0;top:36px;justify-content:center}
.env-back .brand-dot{width:10px;height:10px}
.env-back .brand-name{font-size:12px}
.env-back .address{position:absolute;left:0;right:0;top:193px;text-align:center;font-size:8px;line-height:1.4}
.env-back .address .company{color:var(--red);font-weight:700;font-size:9px}
.env-back .accent{position:absolute;left:184px;width:200px;top:188px;height:1px;background:linear-gradient(90deg,rgba(210,35,42,0),var(--red),rgba(210,35,42,0))}
</style>
</head>
<body>

<section class="sheet letterhead">
  <div class="brand"><span class="brand-dot"></span><span class="brand-name">Bawo Ingredients</span></div>
  <div class="divider"></div>
  <address class="contact">
    <div class="company">PT Bawo Ingredients</div>
    Ruko Puri Lestari Selatan<br>Blok F07 no: 11-12<br>Sunter Jaya Utara, 14350<br>Indonesia
    <div class="gap"></div>
    Tel +62 21 638 2097<br>Fax +62 21 638 2096<br>Email: info@bawo-ingredients.co.id
  </address>
  <div class="web-tab">www.bawo-ingredients.co.id</div>
  <div class="base-line"></div>
</section>

<section class="sheet card-front">
  <div class="brand"><span class="brand-dot"></span><span class="brand-name">Bawo Ingredients</span></div>
  <div class="person">
    <strong>Dimas Santoso</strong>General Director
    <div class="mob">Mob: +62 812 7730 4418<br>Email: info@bawo-ingredients.co.id</div>
  </div>
  <address class="contact">
    <div class="company">PT Bawo Ingredients</div>
    Ruko Puri Lestari Selatan<br>Blok F07 no: 11-12<br>Sunter Jaya Utara, 14350<br>Indonesia
    <div class="gap"></div>
    Tel +62 21 638 2097<br>Fax +62 21 638 2096<br>www.bawo-ingredients.co.id
  </address>
  <div class="web-tab">www.bawo-ingredients.co.id</div>
  <div class="base-line"></div>
</section>

<section class="sheet card-back">
  <div class="brand"><span class="brand-name">Bawo Ingredients</span></div>
  <div class="web">www.bawo-ingredients.co.id</div>
</section>

<section class="sheet env-front">
  <div class="brand"><span class="brand-dot"></span><span class="brand-name">Bawo Ingredients</span></div>
  <div class="web-tab">www.bawo-ingredients.co.id</div>
  <div class="base-line"></div>
</section>

<section class="sheet env-back">
  <svg class="flap" width="569" height="251" viewBox="0 0 569 251" aria-hidden="true">
    <path d="M0 0 L284 100 L569 0" fill="none" stroke="#bdbdbd" stroke-width="1"/>
    <path d="M0 251 L180 110 M569 251 L395 110" fill="none" stroke="#d8d8d8" stroke-width="1"/>
  </svg>
  <div class="brand"><span class="brand-dot"></span><span class="brand-name">Bawo Ingredients</span></div>
  <div class="accent"></div>
  <div class="address">
    <div class="company">PT Bawo Ingredients</div>
    Ruko Puri Lestari Selatan, Blok F07 no: 11-12 Sunter Jaya Utara, 14350 Indonesia<br>
    Tel:+62 21 638 2097 &nbsp;Fax:+62 21 638 2096 &nbsp;Email: info@bawo-ingredients.co.id
  </div>
</section>

</body>
</html>
```